Geschäftspapiere für Jobwebseite
Zielgruppe
Hier finden sie alle Informationen zu unserem Unternehmen:
https://www.sauberwerk-stelle.com
Aufgabenstellung
Gerne von den Farben angelehnt an die Website ein modernes Briefpapier gestalten.

```html
<!DOCTYPE html>
<html lang="de">
<head>
<meta charset="utf-8">
<title>Briefpapier – SAUBERWERK-STELLE.de</title>
<link rel="stylesheet" href="https://fonts.googleapis.com/css2?family=PT+Sans:wght@400;700&display=swap">
<style>
  :root{
    --stage:#ebebeb;
    --paper:#ffffff;
    --brand-green:#27914a;
    --ink:#4a4a4a;
    --ink-dark:#555555;
    --label:#333333;
    --sign:#cfd3e6;
  }
  *{box-sizing:border-box;margin:0;padding:0}
  html,body{width:1200px;height:864px;overflow:hidden;background:var(--stage);
    font-family:"PT Sans",Tahoma,sans-serif;color:var(--ink)}
  .canvas{position:relative;width:1200px;height:864px}
  .view-label{position:absolute;top:66px;font-size:15.5px;color:var(--label);font-weight:400}
  .sheet{position:absolute;top:94px;width:484px;background:var(--paper);
    box-shadow:4px 6px 9px rgba(0,0,0,.28);overflow:hidden}
  .sheet--folded{left:106px;height:242px}
  .sheet--open{left:630px;height:685px}
  .wordmark{position:absolute;left:46px;top:22px;font-size:18px;font-weight:700;
    color:var(--ink-dark);letter-spacing:.2px}
  .sender-box{position:absolute;left:329px;top:0;width:137px;height:152px;
    background:var(--brand-green);color:#fff;padding:26px 0 0 23px;
    font-size:6.4px;line-height:9px}
  .sender-box p{margin-bottom:9px}
  .sender-box strong{font-weight:700}
  .contact-row{display:flex;align-items:center;gap:4px}
  .contact-row svg{width:6px;height:6px;fill:#fff;flex:none}
  .return-line{position:absolute;left:58px;top:123px;font-size:5px;color:var(--ink)}
  .return-line b{color:var(--brand-green);font-weight:700}
  .recipient{position:absolute;left:58px;top:138px;font-size:7.6px;line-height:10.6px}
  .subject{position:absolute;left:58px;top:225px;font-size:10px;font-weight:700;
    color:var(--ink-dark);letter-spacing:.3px}
  .fold-mark{position:absolute;left:0;width:7px;height:1px;background:var(--brand-green)}
  .letter-body{position:absolute;left:58px;top:263px;width:322px;font-size:7.1px;line-height:9.8px}
  .letter-body p{margin-bottom:9.8px}
  .letter-body .salutation{margin-bottom:19px}
  .closing{position:absolute;left:58px;top:568px;font-size:7.1px}
  .signature{position:absolute;left:58px;top:580px;width:100px;height:27px;
    background:linear-gradient(90deg,var(--sign),#eef0f8)}
  .signer{position:absolute;left:58px;top:611px;font-size:7.1px}
  .tagline{position:absolute;left:329px;top:643px;width:137px;height:42px;
    background:var(--brand-green);color:#fff;font-size:7.8px;line-height:11px;
    padding:8px 0 0 12px}
  .footer-band{position:absolute;left:0;bottom:0;width:100%;height:6px;background:var(--brand-green)}
</style>
</head>
<body>
<main class="canvas">

  <h2 class="view-label" style="left:106px">Gefalzter Brief</h2>
  <h2 class="view-label" style="left:630px;top:64px">Geöffneter Brief</h2>

  <!-- folded letter -->
  <section class="sheet sheet--folded">
    <div class="wordmark">SAUBERWERK-STELLE.de</div>
    <aside class="sender-box">
      <p><strong>SAUBERWERK-STELLE.de</strong><br>Gewerbering Nord 7<br>76133 Karlsruhe</p>
      <p>
        <span class="contact-row"><svg viewBox="0 0 10 8"><path d="M0 0h10v1.2L5 4.5 0 1.2zM0 2.4l5 3.3 5-3.3V8H0z"/></svg>info@sauberwerk-stelle.de</span>
        <span class="contact-row"><svg viewBox="0 0 10 10"><path d="M2 0l2 2.6-1.2 1.4a6 6 0 003.2 3.2L7.4 6 10 8l-1.4 2C4 10 0 6 0 1.4z"/></svg>0721 555 014 2</span>
      </p>
      <p>Inhaber<br>Herr Lukas Wendler<br>Amtsgericht Karlsruhe<br>HRB xxxx<br>USt-IdNr. DExxxxxxx</p>
    </aside>
    <div class="return-line"><b>SAUBERWERK-STELLE.DE</b> | Gewerbering Nord 7 | 76133 Karlsruhe</div>
    <address class="recipient" style="font-style:normal">Firma: Musterfirma<br>Herr Maximilian Mustermann<br>Musterstraße 11<br>12345 Musterstadt</address>
    <div class="subject">HIER STEHT DER BETREFF</div>
  </section>

  <!-- open letter -->
  <section class="sheet sheet--open">
    <div class="wordmark">SAUBERWERK-STELLE.de</div>
    <aside class="sender-box">
      <p><strong>SAUBERWERK-STELLE.de</strong><br>Gewerbering Nord 7<br>76133 Karlsruhe</p>
      <p>
        <span class="contact-row"><svg viewBox="0 0 10 8"><path d="M0 0h10v1.2L5 4.5 0 1.2zM0 2.4l5 3.3 5-3.3V8H0z"/></svg>info@sauberwerk-stelle.de</span>
        <span class="contact-row"><svg viewBox="0 0 10 10"><path d="M2 0l2 2.6-1.2 1.4a6 6 0 003.2 3.2L7.4 6 10 8l-1.4 2C4 10 0 6 0 1.4z"/></svg>0721 555 014 2</span>
      </p>
      <p>Inhaber<br>Herr Lukas Wendler<br>Amtsgericht Karlsruhe<br>HRB xxxx<br>USt-IdNr. DExxxxxxx</p>
    </aside>
    <div class="return-line"><b>SAUBERWERK-STELLE.DE</b> | Gewerbering Nord 7 | 76133 Karlsruhe</div>
    <address class="recipient" style="font-style:normal">Firma: Musterfirma<br>Herr Maximilian Mustermann<br>Musterstraße 11<br>12345 Musterstadt</address>
    <div class="subject">HIER STEHT DER BETREFF</div>

    <span class="fold-mark" style="top:242px"></span>
    <span class="fold-mark" style="top:343px"></span>
    <span class="fold-mark" style="top:485px"></span>

    <article class="letter-body">
      <p class="salutation">Sehr geehrter Herr Mustermann,</p>
      <p>Ferem sit, omniendaecte doluptature mo cuptatio. Ebitati ssumqui coria poreici destrum, vidusap elibus qui ipideli tatecabo. Et remporporio di quo ommolup taessit, ius non esequibus et volupiditio optatur ereicat laut et et quae ium int ma sum cori omnimin recus, ent molupti orrores truptassin eos a cor sa sus dolupta sitist laut que plignat.<br>Axim exeribus. Pudit arum ium ipiet in ni od mos ent liciam quunt aborporem verferr uptasim ra de int quunt a inimin et il mi, eaque volo bla volo bea qui ius, sum volo Ibus, acepernatem aut explabo rporupta pa qui consediam atus.</p>
      <p>Aximporporum et dolore conecerferia venimet verae sum nobist asintorest, eosant alique volut qui te nullo eum que velitatatis iumque mint ut volupta tquiatemodi dolless itature, et laccuptae pa invelis sequunt, velique abo. Obis sus et officipsamus premquidi blabo. Dollore rnatend untiatu reperion consequam faccaborit faciates sitatenet harunt invenim di sumque.</p>
      <p>Pore oditam identitiis dit estrunt officta tecust pro maionsequis del mos aut quiatur?<br>Icillab ipsapie nihilluptas mo et que sitatiis dolupta quament laborro cuptae. Namus, utendunt. Pictat. Otae nimet faccatur? Erumqui at occum ratquia nos viti con reiunt volorro ommodit, nusam ratiasr itatet pa quistionsed explitem. Nam inis essinve litatib usdandit miliaspedi aces utatem facia volesci alit evel iuntis unt ab ilit autem quam archilluptae</p>
      <p>Sit laut qui tem rerum as reperae prorempedi neces et acculparum fugiae denetur, torernam verepti issinullenis arum re dolessi sum rerum ra di que vel minciam duntio. Aborios molutae praest, corit quiaerci sus andigente sincius si occum fugiae reperibus delicab is sunt magnam is vento to blandiscia quo dolorro vitasped evelest, suntemp oreictor a porepudaeri que conem aut mint alitam si quae volorro rerferia volorepeliti ad ma voluptat acest estrupta si voloriscid millatatae re, offictis aperor maio. Ut liquam erum eum dunt offici dolenih ilibus, id erro et volupta volectent que pla sitis exped maio. Nam sitatur sit qui comnima ximpore consect ibeatatum aut in nulparc hilite nonsequia autemquat.</p>
    </article>

    <div class="closing">Mit freundlichen Grüßen</div>
    <div class="signature" role="img" aria-label="Handschriftliche Unterschrift"></div>
    <div class="signer">Max Mustermann</div>

    <div class="tagline">Wir begleiten Dich bei Deinem<br>Jobwechsel als Pflegefachkraft!</div>
    <div class="footer-band"></div>
  </section>

</main>
</body>
</html>
```